BildeVOLD buisnesscard

Hey :) I need a modern buisnesscard for my company BildeVOLD
It most have:
Dagligleder og Fotograf: Henrik Audun Strandvik

Mob: +4791264085
Epost: post@bildevold.example
Adresse: Kvernbakken9, 6040 Langevåg

Facbook and instagram logo with text BildeVOLD

BildeVOLD logo

It Company

```html
<!DOCTYPE html>
<html lang="no">
<head>
<meta charset="utf-8">
<title>BildeVOLD business card</title>
<link href="https://fonts.googleapis.com/css2?family=Lato:wght@400;700&display=swap" rel="stylesheet">
<style>
  :root {
    --backdrop: #3b3b3b;
    --paper: #ffffff;
    --stone: #bdbbbc;
    --ink: #111111;
    --muted: #b9b7b8;
  }
  * { margin: 0; padding: 0; box-sizing: border-box; }
  html, body {
    width: 1200px; height: 900px; overflow: hidden;
    background: var(--backdrop);
    font-family: "Lato", sans-serif;
  }
  .canvas {
    position: relative; width: 1200px; height: 900px;
    display: flex; flex-direction: column; align-items: center; justify-content: center; gap: 34px;
  }
  .card {
    position: relative; width: 600px; height: 343px;
    background: var(--paper); overflow: hidden;
    box-shadow: 0 6px 18px rgba(0,0,0,.35);
  }
  .brand-name {
    font-weight: 700; color: var(--stone); letter-spacing: .5px; line-height: 1;
  }
  .card--front { display: flex; align-items: center; justify-content: center; }
  .card--front .brand-name { font-size: 66px; }
  .card--back .brand-name {
    position: absolute; left: 36px; top: 44px; font-size: 46px;
  }
  .card-band {
    position: absolute; left: 0; right: 0; top: 176px; bottom: 0;
    background: linear-gradient(to bottom, rgba(189,187,188,0) 0%, var(--stone) 22%, var(--stone) 100%);
  }
  .holder {
    position: absolute; left: 345px; top: 110px;
  }
  .holder-name { font-size: 22px; color: var(--ink); font-weight: 400; }
  .holder-title { font-size: 13px; color: var(--muted); margin-top: 2px; }
  .contact {
    position: absolute; left: 345px; top: 228px; color: var(--paper);
    font-size: 14px; line-height: 17px;
  }
  .contact-address { margin-bottom: 8px; }
  .contact-list { list-style: none; }
  .contact-list li { display: flex; align-items: center; gap: 8px; }
  .contact-icon { width: 12px; height: 12px; flex: none; }
</style>
</head>
<body>
<main class="canvas">
  <section class="card card--front">
    <div class="brand-name">BildeVOLD</div>
  </section>

  <section class="card card--back">
    <div class="card-band" role="img" aria-label="Decorative grey wave band across the lower card"></div>

    <div class="brand-name">BildeVOLD</div>

    <div class="holder">
      <div class="holder-name">Henrik Audun Strandvik</div>
      <div class="holder-title">Dagligleder og Fotograf</div>
    </div>

    <div class="contact">
      <div class="contact-address">Kvernbakken 9<br>6040 Vestholm</div>
      <ul class="contact-list">
        <li>
          <svg class="contact-icon" viewBox="0 0 12 12" aria-hidden="true"><rect x="3" y="0.5" width="6" height="11" rx="1" fill="none" stroke="#fff"/><line x1="5" y1="10" x2="7" y2="10" stroke="#fff"/></svg>
          +4791264085
        </li>
        <li>
          <svg class="contact-icon" viewBox="0 0 12 12" aria-hidden="true"><rect x="0.5" y="2.5" width="11" height="7" fill="none" stroke="#fff"/><path d="M0.5 2.5 L6 7 L11.5 2.5" fill="none" stroke="#fff"/></svg>
          post@bildevold.example
        </li>
        <li>
          <svg class="contact-icon" viewBox="0 0 12 12" aria-hidden="true"><rect x="1" y="1" width="10" height="10" fill="#fff"/></svg>
          BildeVOLD
        </li>
        <li>
          <svg class="contact-icon" viewBox="0 0 12 12" aria-hidden="true"><circle cx="6" cy="6" r="5" fill="#fff"/></svg>
          BildeVOLD
        </li>
      </ul>
    </div>
  </section>
</main>
</body>
</html>
```